holloway paving service

Needs to have phone number 0418259730 and email markholloway@brightmail.com.au.
ABN 62318470915
name mark holloway

For all your concreting solutions
Excavation
Exposed & colour concrete
House & shed slabs
Driveways
Landing & steps

Contact Information for Business Card

ph 0418259730
email markholloway@brightmail.com.au.
ABN 62318470915
name mark holloway

```html
<!DOCTYPE html>
<html lang="en">
<head>
<meta charset="utf-8">
<title>Holloway Paving Service – Business Card</title>
<link href="https://fonts.googleapis.com/css2?family=Bebas+Neue&family=Lato:wght@400;700&display=swap" rel="stylesheet">
<style>
  :root {
    --backdrop: #2b2b2c;
    --card: #1c1c1d;
    --card-edge: #262627;
    --accent: #f26a21;
    --ink: #f2f2f2;
  }
  * { box-sizing: border-box; margin: 0; padding: 0; }
  html, body { width: 1200px; height: 900px; overflow: hidden; }
  body {
    background: var(--backdrop);
    font-family: "Lato", sans-serif;
    color: var(--ink);
    position: relative;
  }
  .card {
    position: absolute;
    left: 290px;
    width: 620px;
    height: 354px;
    background: linear-gradient(135deg, var(--card) 0%, var(--card-edge) 100%);
    border-radius: 3px;
    overflow: hidden;
  }
  .card--front { top: 70px; }
  .card--back { top: 476px; }

  /* Front */
  .brand {
    position: absolute;
    top: 120px;
    left: 0;
    width: 100%;
    display: flex;
    justify-content: center;
    align-items: center;
    gap: 22px;
  }
  .brand__mark {
    width: 54px; height: 54px;
    background: var(--accent);
  }
  .brand__divider {
    width: 2px; height: 84px;
    background: var(--accent);
  }
  .brand__text { display: flex; flex-direction: column; gap: 6px; }
  .brand__name {
    font-weight: 700;
    font-size: 24px;
    letter-spacing: 1.5px;
    text-transform: uppercase;
    color: var(--accent);
  }
  .brand__phone {
    font-size: 17px;
    letter-spacing: 4px;
    color: var(--accent);
    text-align: center;
  }
  .website {
    position: absolute;
    bottom: 42px;
    left: 0; width: 100%;
    text-align: center;
    font-size: 15px;
  }
  .website__domain { color: var(--accent); }

  /* Back */
  .person {
    position: absolute;
    top: 128px;
    right: 348px;
    text-align: right;
  }
  .person__name {
    font-family: "Bebas Neue", sans-serif;
    font-weight: 400;
    font-size: 44px;
    letter-spacing: 1px;
    color: var(--accent);
    line-height: 1;
    white-space: nowrap;
  }
  .person__role { font-size: 18px; margin-top: 2px; }
  .back__divider {
    position: absolute;
    top: 120px; left: 288px;
    width: 2px; height: 96px;
    background: var(--accent);
  }
  .contacts {
    position: absolute;
    top: 112px; left: 306px;
    list-style: none;
    font-size: 15px;
    line-height: 27px;
  }
  .contacts li { display: flex; align-items: center; gap: 8px; white-space: nowrap; }
  .contacts svg { width: 12px; height: 12px; flex: none; }
  .contacts__spacer { width: 12px; height: 12px; flex: none; }
  .address {
    position: absolute;
    bottom: 52px; left: 0; width: 100%;
    text-align: center;
    font-size: 18px;
  }
  .address__town { color: var(--accent); }
</style>
</head>
<body>
  <section class="card card--front">
    <div class="brand">
      <div class="brand__mark"></div>
      <div class="brand__divider"></div>
      <div class="brand__text">
        <span class="brand__name">Holloway Paving Service</span>
        <span class="brand__phone">0418259730</span>
      </div>
    </div>
    <p class="website">www.<span class="website__domain">hollowaypaving</span>.com.au</p>
  </section>

  <section class="card card--back">
    <div class="person">
      <h1 class="person__name">Mark Holloway</h1>
      <p class="person__role">Director</p>
    </div>
    <div class="back__divider"></div>
    <ul class="contacts">
      <li>
        <svg viewBox="0 0 12 12" aria-hidden="true"><path d="M2.5 1 L4.5 1 L5 3.5 L3.8 4.5 Q5 7 7.5 8.2 L8.5 7 L11 7.5 L11 9.5 Q10.5 11 9 11 Q1 10 1 3 Q1 1.5 2.5 1Z" fill="var(--accent)"/></svg>
        +61 418 259 730
      </li>
      <li>
        <svg viewBox="0 0 12 12" aria-hidden="true"><rect x="1" y="2.5" width="10" height="7" fill="none" stroke="var(--accent)" stroke-width="1.2"/><path d="M1 2.5 L6 6.5 L11 2.5" fill="none" stroke="var(--accent)" stroke-width="1.2"/></svg>
        markholloway@brightmail.com.au
      </li>
      <li>
        <svg viewBox="0 0 12 12" aria-hidden="true"><circle cx="6" cy="6" r="5" fill="none" stroke="var(--accent)" stroke-width="1.1"/><ellipse cx="6" cy="6" rx="2.2" ry="5" fill="none" stroke="var(--accent)" stroke-width="1"/><path d="M1 6 H11" stroke="var(--accent)" stroke-width="1"/></svg>
        <span>www.<span class="website__domain">hollowaypaving</span>.com.au</span>
      </li>
      <li>
        <span class="contacts__spacer"></span>
        <span><span class="website__domain">ABN</span> 62318470915</span>
      </li>
    </ul>
    <p class="address"><span class="address__town">Ashcombe :</span> Lindale, Tasmania 7031</p>
  </section>
</body>
</html>
```